Business card design for sustainable building and development company

Need a business card design for a new sustainable building and real estate development company in the San Francisco Bay area. Name of company is "Tovrin Advisors, LLC" and we provide "Sustainable building, energy and development services" for residential and non residential projects. We'd like the following colors used but not all area required: green, gray, blue. Design should communicate innovation, professionalism and sustainability. Our current website is www.tovrin-advisors.example. Another possible design idea is to have the following listed on the back of the card:
Certified: VERN QS, Eco Marker Rater, DOLM Rater, Terravue Inspector, KSO TQ Building Analyst. Its not a must but could be text that could be used for back of card. Overall, we are open to a simple, clean design and or one with more text than usual for a card.

Industry/Entity Type

Real Estate

Contact Information for Business Card

Name on card: Mark J. Halvik
Title for Name: Principal + Founder
Phone: 555.814.0627
Email: mhalvik@tovrin-advisors.example
Website: www.tovrin-advisors.example

Also, please add the following for address:
San Francisco, California

Requirements
Nice to have
• If you can integrate the outline of a skyline on the backside of the card and if it looks good, I would like to see the design
Should not have
• a barcode;

```html
<!DOCTYPE html>
<html lang="en">
<head>
<meta charset="utf-8">
<title>Tovrin Advisors – Business Card</title>
<link rel="stylesheet" href="https://fonts.googleapis.com/css2?family=Montserrat:wght@500;700&family=Tinos&display=swap">
<style>
  :root {
    --canvas-bg: #e9ebe8;
    --card-bg: #ffffff;
    --brand-green: #6cc24a;
    --brand-green-dark: #5cb13c;
    --ink: #1f1f1f;
    --ink-soft: #3a3a3a;
    --stripe-gray: #bfc3c0;
    --on-green: #ffffff;
  }
  * { box-sizing: border-box; margin: 0; padding: 0; }
  html, body { width: 1200px; height: 900px; overflow: hidden; }
  body { background: var(--canvas-bg); position: relative; }

  .card {
    position: absolute;
    width: 665px;
    height: 380px;
    left: 268px;
    background: var(--card-bg);
    border-radius: 32px;
    overflow: hidden;
    box-shadow: 0 10px 28px rgba(0,0,0,0.12);
  }
  .card--back { top: 45px; }
  .card--front { top: 475px; }

  .card__art { position: absolute; inset: 0; width: 100%; height: 100%; }

  .brand {
    position: absolute;
    display: flex;
    flex-direction: column;
    align-items: center;
    text-align: center;
  }
  .brand__mark {
    width: 64px; height: 64px;
    border-radius: 50%;
    background: var(--brand-green);
    margin-bottom: 8px;
  }
  .brand__name {
    font-family: "Montserrat", sans-serif;
    font-weight: 700;
    font-size: 34px;
    line-height: 1;
    color: var(--brand-green);
    letter-spacing: -0.5px;
  }
  .brand__tagline {
    font-family: "Montserrat", sans-serif;
    font-weight: 500;
    font-size: 9.5px;
    letter-spacing: 0.2px;
    color: var(--ink-soft);
    margin-top: 5px;
    text-transform: uppercase;
  }
  .card--back .brand { left: 0; right: 0; top: 115px; }
  .card--back .brand__mark { width: 78px; height: 78px; }
  .card--back .brand__name { font-size: 40px; }
  .card--back .brand__tagline { font-size: 11px; }

  .card--front .brand { left: 290px; width: 340px; top: 62px; }

  .person {
    position: absolute;
    left: 350px;
    width: 220px;
    top: 210px;
    text-align: center;
    font-family: "Tinos", serif;
    color: var(--ink-soft);
  }
  .person__name { font-size: 22px; }
  .person__title { font-size: 18px; margin-top: 6px; }

  .contact {
    position: absolute;
    left: 28px;
    top: 128px;
    list-style: none;
    font-family: "Tinos", serif;
    font-size: 13px;
    line-height: 1.2;
    color: var(--on-green);
  }
  .contact__item { display: flex; align-items: flex-start; margin-bottom: 8px; }
  .contact__icon { flex: 0 0 14px; width: 14px; height: 14px; margin-right: 7px; margin-top: 1px; }
  .contact__lines span { display: block; }
</style>
</head>
<body>

  <section class="card card--back" aria-label="Card back">
    <div class="brand">
      <span class="brand__mark"></span>
      <span class="brand__name">Tovrin Advisors</span>
      <span class="brand__tagline">Sustainable building, energy &amp; development services</span>
    </div>
  </section>

  <section class="card card--front" aria-label="Card front">
    <svg class="card__art" viewBox="0 0 665 380" preserveAspectRatio="none" aria-hidden="true">
      <path class="wave-green" fill="var(--brand-green)"
        d="M0,70 C110,40 170,110 215,215 C260,320 380,352 665,332 L665,380 L0,380 Z"/>
      <path class="wave-stripe-dark" fill="var(--ink)"
        d="M40,38 C150,20 205,95 250,200 C295,305 420,338 665,316 L665,324 C410,346 283,315 236,205 C192,102 140,34 40,38 Z"/>
      <path class="wave-stripe-gray" fill="var(--stripe-gray)"
        d="M20,56 C130,32 190,104 235,208 C280,312 400,342 665,324 L665,330 C395,350 270,318 226,212 C182,110 126,42 20,56 Z"/>
      <path class="wave-stripe-base" fill="var(--ink)"
        d="M300,358 C420,372 540,362 665,346 L665,356 C540,372 420,378 300,358 Z"/>
    </svg>

    <div class="brand">
      <span class="brand__mark"></span>
      <span class="brand__name">Tovrin Advisors</span>
      <span class="brand__tagline">Sustainable building, energy &amp; development services</span>
    </div>

    <div class="person">
      <p class="person__name">Mark J. Halvik</p>
      <p class="person__title">Owner / C.E.O</p>
    </div>

    <ul class="contact">
      <li class="contact__item">
        <svg class="contact__icon" viewBox="0 0 14 14" aria-hidden="true"><circle cx="7" cy="7" r="7" fill="#fff"/><path d="M7 3.2a2.4 2.4 0 0 0-2.4 2.4C4.6 7.4 7 10.6 7 10.6s2.4-3.2 2.4-5A2.4 2.4 0 0 0 7 3.2z" fill="var(--brand-green-dark)"/></svg>
        <div class="contact__lines"><span>Suite # 410, Oak Bldg,</span><span>CA 94000</span></div>
      </li>
      <li class="contact__item">
        <svg class="contact__icon" viewBox="0 0 14 14" aria-hidden="true"><circle cx="7" cy="7" r="7" fill="#fff"/><path d="M4.6 3.6l1.4 0 .6 1.8-.9.7a5 5 0 0 0 2.2 2.2l.7-.9 1.8.6 0 1.4c0 .4-.3.6-.7.6A6.2 6.2 0 0 1 4 4.3c0-.4.2-.7.6-.7z" fill="var(--brand-green-dark)"/></svg>
        <div class="contact__lines"><span>555-201-7890</span><span>555-654-3210</span><span>555-789-1230</span></div>
      </li>
      <li class="contact__item">
        <svg class="contact__icon" viewBox="0 0 14 14" aria-hidden="true"><circle cx="7" cy="7" r="7" fill="#fff"/><rect x="3.5" y="4.5" width="7" height="5" rx="0.6" fill="var(--brand-green-dark)"/></svg>
        <div class="contact__lines"><span>name@sampledomain.example</span><span>www.sampledomain.example</span></div>
      </li>
    </ul>
  </section>

</body>
</html>
```